Fresh Dwelling Tract Guide needs a new Landing Page

I like to get a landing page or website with 2-3 pages to help target home buyers who are looking to buy homes from builders such as TW Residences, Morvik, P.L. Fennick, etc. The landing page/website to be non-cluttered and be able to explain to home buyers that there are many benefits to include me as their buyer's agent when they buy a brand new home from any builders.
I may want to incorporate a short explanation video (animated) on the landing page and then for the viewer to click on a button that will take them to another page where they can search for new homes from different builders.
Target Market(s)
Home buyers looking to buy brand new home from builders such as TW Residences, Morvik, P.L. Fennick, etc.
Industry/Entity Type
Real Estate
Number of Pages Required
2 page
Font styles to use
Requirements
Must have
- The landing page may have the explanation video at the bottom of the landing page (scrolled down) or there may be a CALL TO ACTION button that takes the viewer to the 2nd page to watch the explanation video. Once they watched the explanation video and are still interested, they can click on another CALL TO ACTION button that will take them to another website that they will be able to search for all the available new homes and register their contact information.
Should not have
- No clutters and no dark colors.

```html
<!DOCTYPE html>
<html lang="en">
<head>
<meta charset="utf-8">
<title>Fresh Dwelling Tract Guide</title>
<link href="https://fonts.googleapis.com/css2?family=Oswald:wght@400&family=Poppins:wght@300;400;500;600&display=swap" rel="stylesheet">
<style>
  :root {
    --sky-top: #0a5cf5;
    --sky-mid: #2f7ee6;
    --sky-low: #8aa6c8;
    --house: #b8a68c;
    --ground: #2b2a24;
    --grass: #2f3526;
    --accent-red: #ff0d0d;
    --white: #ffffff;
    --thumb-a: #6d8a5a;
    --thumb-b: #9aa5a8;
    --thumb-c: #8c7a64;
  }
  * { margin: 0; padding: 0; box-sizing: border-box; }
  html, body { width: 1200px; height: 753px; overflow: hidden; }
  body { font-family: "Poppins", sans-serif; color: var(--white); }
  .hero {
    position: relative; width: 1200px; height: 753px; overflow: hidden;
  }
  .hero-photo {
    position: absolute; inset: 0;
    background:
      linear-gradient(180deg, var(--sky-top) 0%, var(--sky-mid) 22%, var(--sky-low) 38%, var(--house) 52%, #5b5444 64%, var(--ground) 72%, var(--grass) 85%, #252a1f 100%);
  }
  .site-header { position: absolute; top: 0; left: 0; right: 0; height: 78px; }
  .brand {
    position: absolute; left: 99px; top: 22px;
    font-family: "Oswald", sans-serif; font-size: 27px; line-height: 34px;
    text-transform: uppercase; letter-spacing: 0.2px; color: var(--white);
  }
  .contact-btn {
    position: absolute; left: 903px; top: 17px; width: 147px; height: 42px;
    background: var(--accent-red); color: var(--white);
    font-size: 14px; font-weight: 500; letter-spacing: 0.4px;
    display: flex; align-items: center; justify-content: center; text-decoration: none;
  }
  .menu-toggle { position: absolute; left: 1082px; top: 31px; width: 19px; height: 16px; }
  .hero-copy { position: absolute; top: 128px; left: 0; right: 0; text-align: center; }
  .hero-title { font-size: 45px; font-weight: 600; line-height: 60px; }
  .hero-sub { font-size: 15px; font-weight: 300; margin-top: 2px; }
  .play-btn { position: absolute; left: 546px; top: 290px; width: 108px; height: 108px; }
  .slider-meta { position: absolute; left: 101px; top: 568px; }
  .slide-count { font-size: 15px; letter-spacing: 1px; }
  .slide-label { font-size: 17px; letter-spacing: 0.8px; margin-top: 14px; }
  .slider-arrow { position: absolute; top: 580px; width: 12px; height: 18px; }
  .slider-arrow.prev { left: 625px; }
  .slider-arrow.next { left: 1138px; z-index: 2; }
  .thumb { position: absolute; top: 535px; width: 160px; height: 109px; }
  .thumb-1 { left: 673px; background: linear-gradient(180deg, #2a64c8 0%, var(--thumb-a) 55%, #7c8a86 100%); }
  .thumb-2 { left: 870px; background: linear-gradient(180deg, #d9e3ee 0%, var(--thumb-b) 55%, #6f9a4a 100%); }
  .thumb-3 { left: 1067px; background: linear-gradient(180deg, #5a7fb3 0%, var(--thumb-c) 55%, #a89a86 100%); }
  .social { position: absolute; top: 697px; left: 0; right: 0; display: flex; justify-content: center; gap: 38px; }
  .social-link { width: 16px; height: 16px; border: 2px solid var(--white); border-radius: 50%; display: block; }
  .copyright { position: absolute; top: 729px; left: 0; right: 0; text-align: center; font-size: 11.5px; font-weight: 300; }
</style>
</head>
<body>
<main class="hero">
  <div class="hero-photo" role="img" aria-label="Large modern stone and stucco house at dusk with landscaped garden, blue sky and trees"></div>

  <header class="site-header">
    <div class="brand">Fresh Dwelling Tract Guide</div>
    <a class="contact-btn" href="#">CONTACT US</a>
    <svg class="menu-toggle" viewBox="0 0 19 16" aria-label="Menu">
      <rect x="0" y="0" width="19" height="3.2" fill="#fff"/>
      <rect x="0" y="6.4" width="19" height="3.2" fill="#fff"/>
      <rect x="0" y="12.8" width="19" height="3.2" fill="#fff"/>
    </svg>
  </header>

  <section class="hero-copy">
    <h1 class="hero-title">Fresh Dwelling Tract Guide</h1>
    <p class="hero-sub">Lorem ipsum dolor sit amet, consectetur adipiscing elit, sed do eiusmod tempor incididunt</p>
  </section>

  <svg class="play-btn" viewBox="0 0 108 108" aria-label="Play video">
    <circle cx="54" cy="54" r="54" fill="rgba(40,40,40,0.55)"/>
    <circle cx="54" cy="54" r="41" fill="#fff"/>
    <path d="M45 40 L70 54 L45 68 Z" fill="#111"/>
  </svg>

  <div class="slider-meta">
    <div class="slide-count">1/20</div>
    <div class="slide-label">Recent Selling Properties</div>
  </div>

  <svg class="slider-arrow prev" viewBox="0 0 12 18" aria-label="Previous">
    <path d="M10 2 L3 9 L10 16" fill="none" stroke="#fff" stroke-width="2.4"/>
  </svg>
  <div class="thumb thumb-1" role="img" aria-label="Street of colourful suburban houses"></div>
  <div class="thumb thumb-2" role="img" aria-label="Row of grey new-build homes with lawns"></div>
  <div class="thumb thumb-3" role="img" aria-label="Two-storey home with garage"></div>
  <svg class="slider-arrow next" viewBox="0 0 12 18" aria-label="Next">
    <path d="M2 2 L9 9 L2 16" fill="none" stroke="#fff" stroke-width="2.4"/>
  </svg>

  <nav class="social" aria-label="Social links">
    <a class="social-link" href="#" aria-label="Social link 1"></a>
    <a class="social-link" href="#" aria-label="Social link 2"></a>
    <a class="social-link" href="#" aria-label="Social link 3"></a>
    <a class="social-link" href="#" aria-label="Social link 4"></a>
  </nav>

  <footer class="copyright">© 2018 Fresh Dwelling Tract Guide. All Rights Reserved.</footer>
</main>
</body>
</html>
```